Road Construction Company needs business cards

We would like a new business card designed for our business.

We're a road construction company based in Qld, Australia.

Can the business card please have the following information on it.

Name: Warren Halbeck
Position: General Manager
Phone: 0472 915 348
Email: Warren.halbeck@tovrin.com.au
Address: 87 Marrow Ave, Pendlebay, QLD, 4023
Website: www.tovrin.com.au

Visually we'd like the card to be professional and simple.

Attached is our logo.

Our website is www.tovrin.com.au

Target Market(s)

Men aged 25-60

Contact Information for Business Card

As listed in project description

Font styles to use
Serif

Requirements
Must have
• Large logo on back of card

```html
<!DOCTYPE html>
<html lang="en">
<head>
<meta charset="utf-8">
<title>Tovrin Business Card</title>
<link rel="stylesheet" href="https://fonts.googleapis.com/css2?family=Open+Sans:wght@400;700;800&display=swap">
<style>
  :root {
    --stage: #232323;
    --brand-blue: #1457a6;
    --accent-blue: #45a6dc;
    --paper: #ffffff;
    --ink: #1a1a1a;
  }
  * { box-sizing: border-box; margin: 0; padding: 0; }
  html, body {
    width: 1200px; height: 780px; overflow: hidden;
    background: var(--stage);
    font-family: "Open Sans", Arial, sans-serif;
  }
  .canvas {
    position: relative; width: 1200px; height: 780px;
    display: flex; align-items: center; justify-content: center; gap: 40px;
  }
  .card {
    position: relative; width: 540px; height: 309px;
    box-shadow: 0 10px 24px rgba(0,0,0,.55);
  }
  .card-back { background: var(--brand-blue); }
  .card-back .wordmark {
    position: absolute; left: 0; right: 0; top: 108px;
    text-align: center;
    font-size: 78px; font-weight: 800; letter-spacing: 2px;
    color: var(--paper); line-height: 1;
  }
  .card-front { background: var(--paper); }
  .card-front .wordmark {
    position: absolute; left: 34px; top: 44px;
    font-size: 46px; font-weight: 800; letter-spacing: 1px;
    color: var(--brand-blue); line-height: 1;
  }
  .identity {
    position: absolute; right: 34px; top: 26px; text-align: right;
  }
  .identity .name {
    font-size: 22px; font-weight: 700; color: var(--brand-blue); line-height: 1.15;
  }
  .identity .role {
    font-size: 13px; color: var(--ink); letter-spacing: .3px;
  }
  .accent-bar {
    position: absolute; right: 0; top: 24px; width: 18px; height: 40px;
    background: var(--accent-blue);
  }
  .address {
    position: absolute; left: 34px; top: 188px;
    font-size: 13px; line-height: 1.35; color: var(--ink);
  }
  .contacts {
    position: absolute; left: 34px; top: 234px; list-style: none;
    font-size: 13px; line-height: 1.4; color: var(--ink);
  }
  .contacts li { display: flex; align-items: center; gap: 8px; }
  .contacts svg { width: 12px; height: 12px; flex: none; }
</style>
</head>
<body>
<main class="canvas">
  <section class="card card-back" aria-label="Card back">
    <div class="wordmark">TOVRIN</div>
  </section>

  <section class="card card-front" aria-label="Card front">
    <div class="wordmark">TOVRIN</div>
    <div class="accent-bar"></div>
    <div class="identity">
      <div class="name">Warren Halbeck</div>
      <div class="role">General Manager</div>
    </div>
    <p class="address">87 Marrow Ave,<br>Pendlebay, QLD, 4023</p>
    <ul class="contacts">
      <li>
        <svg viewBox="0 0 12 12" aria-hidden="true"><path d="M2.5 1 L4.5 1 L5 3.5 L3.8 4.4 Q5 7 7.6 8.2 L8.5 7 L11 7.5 L11 9.5 Q10.5 11 9 11 Q1 10 1 3 Q1 1.5 2.5 1Z" fill="#45a6dc"/></svg>
        0472 915 348
      </li>
      <li>
        <svg viewBox="0 0 12 12" aria-hidden="true"><rect x="1" y="3" width="10" height="7" fill="none" stroke="#45a6dc" stroke-width="1.2"/><path d="M1 3 L6 7 L11 3" fill="none" stroke="#45a6dc" stroke-width="1.2"/></svg>
        www.tovrin.com.au
      </li>
      <li>
        <svg viewBox="0 0 12 12" aria-hidden="true"><circle cx="6" cy="6" r="5" fill="none" stroke="#45a6dc" stroke-width="1.2"/><ellipse cx="6" cy="6" rx="2.2" ry="5" fill="none" stroke="#45a6dc" stroke-width="1"/><path d="M1 6 H11" stroke="#45a6dc" stroke-width="1"/></svg>
        Warren.halbeck@tovrin.com.au
      </li>
    </ul>
  </section>
</main>
</body>
</html>
```